Road Construction Company needs business cards

We would like a new business card designed for our business.

We're a road construction company based in Qld, Australia.

Can the business card please have the following information on it.

Name: Warren Halbeck
Position: General Manager
Phone: 0472 915 348
Email: Warren.halbeck@tovrin.com.au
Address: 87 Marrow Ave, Pendlebay, QLD, 4023
Website: www.tovrin.com.au

Visually we'd like the card to be professional and simple.

Attached is our logo.

Our website is www.tovrin.com.au

Target Market(s)

Men aged 25-60

Contact Information for Business Card

As listed in project description

Font styles to use
Serif

Requirements
Must have
• Large logo on back of card

```html
<!DOCTYPE html>
<html lang="en">
<head>
<meta charset="utf-8">
<title>Tovrin Business Card</title>
<link rel="stylesheet" href="https://fonts.googleapis.com/css2?family=Montserrat:wght@400;500;700;800&display=swap">
<style>
  :root {
    --bg: #3c3c3c;
    --brand-blue: #0452a3;
    --dark-blue: #0b4fa0;
    --light-blue: #2a9ad8;
    --ink: #161616;
    --paper: #ffffff;
  }
  * { margin: 0; padding: 0; box-sizing: border-box; }
  html, body { width: 1200px; height: 900px; overflow: hidden; }
  body {
    background: var(--bg);
    font-family: "Montserrat", Arial, sans-serif;
    position: relative;
  }
  .card {
    position: absolute;
    width: 680px;
    height: 390px;
    box-shadow: 0 10px 24px rgba(0,0,0,0.45);
  }
  .card-front {
    left: 110px;
    top: 50px;
    background: var(--brand-blue);
    display: flex;
    align-items: center;
    justify-content: center;
  }
  .front-wordmark {
    color: var(--paper);
    font-weight: 800;
    font-size: 112px;
    letter-spacing: 6px;
  }
  .card-back {
    left: 410px;
    top: 470px;
    background: var(--paper);
  }
  .back-wordmark {
    position: absolute;
    right: 48px;
    top: 44px;
    color: var(--dark-blue);
    font-weight: 800;
    font-size: 52px;
    letter-spacing: 3px;
  }
  .person {
    position: absolute;
    left: 48px;
    top: 150px;
  }
  .person-name {
    font-weight: 700;
    font-size: 27px;
    letter-spacing: 0.5px;
    color: var(--dark-blue);
  }
  .person-name .first { color: var(--light-blue); }
  .person-role {
    font-size: 19px;
    font-weight: 500;
    color: var(--ink);
    margin-top: 2px;
  }
  .address {
    position: absolute;
    right: 48px;
    top: 170px;
    font-size: 18px;
    font-weight: 500;
    color: var(--ink);
    line-height: 1.35;
  }
  .contacts {
    position: absolute;
    left: 48px;
    bottom: 34px;
    list-style: none;
    font-size: 19px;
    font-weight: 500;
    color: var(--ink);
  }
  .contacts li {
    display: flex;
    align-items: center;
    gap: 12px;
    line-height: 1.45;
  }
  .contacts svg { width: 20px; height: 20px; flex: none; }
</style>
</head>
<body>
  <section class="card card-front">
    <span class="front-wordmark">TOVRIN</span>
  </section>

  <section class="card card-back">
    <span class="back-wordmark">TOVRIN</span>

    <div class="person">
      <div class="person-name"><span class="first">WARREN</span> HALBECK</div>
      <div class="person-role">General Manager</div>
    </div>

    <div class="address">
      87 Marrow Ave<br>
      Pendlebay, QLD, 4023
    </div>

    <ul class="contacts">
      <li>
        <svg viewBox="0 0 20 20" aria-hidden="true">
          <path d="M2 7c0-2 3-4 8-4s8 2 8 4v1.5h-4V6.5H6v2H2z" fill="var(--dark-blue)"/>
          <path d="M4 10h12l1 7H3z" fill="var(--dark-blue)"/>
          <circle cx="10" cy="13.5" r="2" fill="#fff"/>
        </svg>
        0472 915 348
      </li>
      <li>
        <svg viewBox="0 0 20 20" aria-hidden="true">
          <rect x="1" y="4" width="18" height="12" fill="var(--dark-blue)"/>
          <path d="M1 4l9 7 9-7" fill="none" stroke="#fff" stroke-width="1.5"/>
        </svg>
        Warren.halbeck@tovrin.com.au
      </li>
      <li>
        <svg viewBox="0 0 20 20" aria-hidden="true">
          <circle cx="10" cy="10" r="8.5" fill="var(--dark-blue)"/>
          <path d="M1.5 10h17M10 1.5v17" stroke="#fff" stroke-width="1.2"/>
          <ellipse cx="10" cy="10" rx="4" ry="8.5" fill="none" stroke="#fff" stroke-width="1.2"/>
        </svg>
        www.tovrin.com.au
      </li>
    </ul>
  </section>
</body>
</html>
```